Hop Along Days campaign: promoting kids play in the UK - Website Redesign

Hop Along Days is a national UK campaign that promotes the value of play for children. The current website is live at http://www.hopalongdays.co.uk. This website has been live for 4 years and now needs to be redesigned. The target audience is parents of young children up to the age of 12.

The current site was designed with a series of old adverts in mind. Here is an example of an old advert: http://vidshare.example/qR7tLm2XwZa

Criticisms of existing site:
The design represented the adverts too closely. The result was a website that mirrors the adverts rather than complements them.
The color scheme is too dark.
Text-heavy pages (e.g. http://www.hopalongdays.co.uk/fun.php) are dull and not FUN!

New site
We have recently had a series of new video adverts produced:
advert 1: http://vidshare.example/hB4nVc8JsPe
advert 2: http://vidshare.example/KgW3rTy9DuM
advert 3: http://vidshare.example/zA5oEi1HbNq

The new site should be cleaner and brighter than the existing site, possibly with a white background using graphics, fonts and advert characters (see attached character graphics files) to add the element of fun and play.

The homepage should include:
1. Hop Along Days logo (attached)
2. Social Media links (visible on all pages of the site) – Chatterbook, Chirpline, ClipVault
3. Link to the HopAlongDays app page of the site (visible on all pages)
4. Image/video placeholder that the user can scroll through, view full-size images and play videos.
5. Text area to hold approximately 100 words describing the purpose of the campaign
6. Site footer to contain the same information as on the existing site along with the Northern Games & Crafts Guild logo (attached)

Site structure:
One change to the site structure… the “Brought to you by” menu item will be removed from the top-level menu.

General:
Some pages on the existing site are quite text-heavy, we would like to break up text on these pages in some way. Graphical division of paragraphs, use of advert characters?

Please note that all attached graphics file are the property of the Northern Games & Crafts Guild and must only be used for the purpose of this project.

```html
<!DOCTYPE html>
<html lang="en">
<head>
<meta charset="utf-8">
<title>Hop Along Days</title>
<link href="https://fonts.googleapis.com/css2?family=Anton&family=Kalam:wght@400;700&family=Open+Sans:wght@400&family=Parisienne&display=swap" rel="stylesheet">
<style>
  :root {
    --green: #558d0b;
    --yellow: #f4e11a;
    --white: #ffffff;
    --purple: #5f3e9a;
    --pink: #ef5d86;
    --blue: #1cb4e8;
    --grey: #6f6f6f;
    --body-text: #555555;
    --sky-top: #bfe2f3;
    --sky-mid: #e8f4fa;
    --grass: #8cc63f;
  }
  * { margin: 0; padding: 0; box-sizing: border-box; }
  html, body { width: 1200px; height: 1108px; overflow: hidden; background: var(--white); }
  body { position: relative; font-family: "Open Sans", sans-serif; }

  .site-header {
    position: absolute; left: 0; top: 0; width: 1200px; height: 113px;
    background: var(--green);
  }
  .brand {
    position: absolute; left: 38px; top: 34px;
    font-family: "Kalam", cursive; font-weight: 700; font-size: 30px;
    color: var(--white); line-height: 1;
  }
  .main-nav { position: absolute; top: 56px; left: 0; }
  .main-nav a {
    position: absolute; white-space: nowrap;
    font-family: "Kalam", cursive; font-weight: 700; font-size: 23px;
    color: var(--white); text-decoration: none; line-height: 1;
  }
  .main-nav a.is-current { color: var(--yellow); }
  .main-nav a.is-current::after {
    content: ""; position: absolute; left: 0; right: 0; bottom: -12px;
    height: 2px; background: var(--yellow);
  }
  .social-links {
    position: absolute; right: 96px; top: 24px;
    display: flex; gap: 10px;
    font-family: "Kalam", cursive; font-weight: 700; font-size: 12px;
  }
  .social-links a { color: var(--white); text-decoration: none; }
  .app-link { position: absolute; left: 1113px; top: 21px; }

  .hero {
    position: absolute; left: 0; top: 113px; width: 1200px; height: 641px; overflow: hidden;
  }
  .hero-scene {
    position: absolute; inset: 0;
    background:
      linear-gradient(to bottom, transparent 0%, transparent 80%, #b5dc63 86%, var(--grass) 100%),
      linear-gradient(to bottom, var(--sky-top) 0%, var(--sky-mid) 55%, #f4f9fb 78%);
  }
  .hero-title {
    position: absolute; left: 478px; top: 30px; width: 400px;
    font-family: "Anton", sans-serif; font-weight: 400; text-align: center;
    font-size: 138px; line-height: 152px; letter-spacing: 1px;
  }
  .hero-title span { display: block; }
  .hero-title .word-one { color: var(--purple); }
  .hero-title .word-two { color: var(--pink); }
  .hero-title .word-three { color: var(--blue); }
  .hero-controls { position: absolute; left: 900px; top: 90px; }
  .hero-quote {
    position: absolute; left: 912px; top: 286px; width: 260px;
    font-family: "Parisienne", cursive; font-size: 24px; line-height: 58px;
    color: var(--purple);
  }
  .hero-caption {
    position: absolute; left: 352px; top: 513px;
    font-family: "Kalam", cursive; font-size: 21px; color: var(--pink);
  }

  .intro { position: absolute; left: 100px; top: 790px; width: 1000px; text-align: center; }
  .intro h1 {
    font-family: "Anton", sans-serif; font-weight: 400; font-size: 40px;
    color: var(--purple); line-height: 1.1; margin-bottom: 22px;
  }
  .intro p {
    font-size: 12.5px; line-height: 22px; color: var(--body-text); margin-bottom: 13px;
  }

  .site-footer {
    position: absolute; left: 0; top: 1014px; width: 1200px; height: 94px;
    background: var(--green);
    font-family: "Kalam", cursive; font-size: 17px; color: var(--white);
  }
  .footer-address { position: absolute; left: 38px; top: 34px; }
  .footer-disclaimer { position: absolute; left: 329px; top: 34px; color: var(--yellow); text-decoration: none; }
  .footer-guild {
    position: absolute; left: 560px; top: 22px; width: 80px; text-align: center;
    font-family: "Kalam", cursive; font-weight: 700; font-size: 13px; line-height: 16px;
  }
  .footer-copyright { position: absolute; right: 38px; top: 34px; }
</style>
</head>
<body>
  <header class="site-header">
    <div class="brand">Hop Along Days</div>
    <nav class="main-nav">
      <a href="#" class="is-current" style="left:317px">Play Right Now</a>
      <a href="#" style="left:520px">Get Involved</a>
      <a href="#" style="left:690px">Why Play</a>
      <a href="#" style="left:829px">Fun Forever</a>
      <a href="#" style="left:995px">Resources</a>
    </nav>
    <div class="social-links">
      <a href="#">Chatterbook</a>
      <a href="#">Chirpline</a>
      <a href="#">ClipVault</a>
    </div>
    <a class="app-link" href="#" aria-label="HopAlongDays app">
      <svg width="50" height="78" viewBox="0 0 50 78">
        <rect x="1" y="1" width="48" height="76" rx="7" fill="#5f3e9a"/>
        <rect x="5" y="11" width="40" height="52" rx="2" fill="#ffffff"/>
        <rect x="18" y="5" width="14" height="2.5" rx="1.2" fill="#8e78c0"/>
        <circle cx="25" cy="70" r="3.5" fill="#8e78c0"/>
      </svg>
    </a>
  </header>

  <section class="hero">
    <div class="hero-scene" role="img" aria-label="Illustrated sky with clouds over green hills, a smiling girl in pink dungarees on the left and four children holding hands on the right"></div>
    <h2 class="hero-title">
      <span class="word-one">Hop</span>
      <span class="word-two">Along</span>
      <span class="word-three">Days</span>
    </h2>
    <svg class="hero-controls" width="140" height="170" viewBox="0 0 140 170" aria-label="Play video">
      <circle cx="98" cy="45" r="39" fill="none" stroke="#6f6f6f" stroke-width="6"/>
      <path d="M90 31 L110 45 L90 59 Z" fill="#6f6f6f"/>
      <path d="M8 150 C30 165 58 150 66 108" fill="none" stroke="#f4e11a" stroke-width="2.5" stroke-linecap="round"/>
      <path d="M56 118 L66 106 L74 120" fill="none" stroke="#f4e11a" stroke-width="2.5" stroke-linecap="round" stroke-linejoin="round"/>
    </svg>
    <p class="hero-quote">It is widely recognised that play is essential for a developing child</p>
    <p class="hero-caption">in physical activity and the link with body image.</p>
  </section>

  <main class="intro">
    <h1>Play Therapy</h1>
    <p>As an intrinsic part of childhood toys play many different roles: from comforters to imaginary friends; tools for cooperative play to exploratory construction. They can also be of immense use in educational and therapeutic environments where play therapy is an integral part of helping children cope with difficult or challenging situations.</p>
    <p>We thought you might be interested in this aspect of play so we asked the experts at WRCH (Westbridge Royal Children's Hospital) and Kindhaven to discover how appropriate toys can really help children who may be facing a change in family circumstances, a medical procedure or long-term health issues.</p>
  </main>

  <footer class="site-footer">
    <span class="footer-address">14 Larkfield Lane, Leeds, LS7 2QP</span>
    <a class="footer-disclaimer" href="#">Click here to read the disclaimer</a>
    <div class="footer-guild">Northern Games &amp; Crafts Guild</div>
    <span class="footer-copyright">© 2014 Northern Games &amp; Crafts Guild Ltd. All Rights Reserved</span>
  </footer>
</body>
</html>
```